VORTEQ

It’s is a startup business. We design and build new products.

Target Market(s)

For my first two products, they are targeting the laundry market, hanger accessory, and new modern style clothes dryer. I also have a Pet Treat product at patent stage, and there are other products not yet started but will be more engineering based. Therefore from young adults to older population

Industry/Entity Type

Colours of website to match the logo (att)

Coding

Coded - Design and coding required

Number of Pages Required

1 page

Font styles to use
Other font styles liked:
• Some of the same font as the logo

Colors

Designer to choose colors to be used in the design.

Requirements
Must have
• An upbeat vibe - the logo looks great so inline with that !
Should not have
• anything old fashioned and old style fonts

```html
<!DOCTYPE html>
<html lang="en">
<head>
<meta charset="utf-8">
<title>VORTEQ – Innovative Products for Everyday Life</title>
<link href="https://fonts.googleapis.com/css2?family=Michroma&family=Roboto:wght@400;500;700&display=swap" rel="stylesheet">
<style>
:root{
  --navy:#232a7a;
  --navy-deep:#1b2168;
  --teal:#00c9cc;
  --teal-soft:#16b6c6;
  --ink:#1e1e2a;
  --body:#444a55;
  --mist:#f3f9f9;
  --foot:#f0f1f7;
  --line:#d9dbe3;
  --grad:linear-gradient(90deg,var(--navy) 0%,#1f4f97 50%,var(--teal) 100%);
}
*{box-sizing:border-box;margin:0;padding:0}
html,body{width:1200px;height:4105px;overflow:hidden;background:#fff}
body{font-family:"Roboto",sans-serif;color:var(--body)}
.canvas{position:relative;width:1200px;height:4105px;overflow:hidden}
.abs{position:absolute}
.display{font-family:"Michroma",sans-serif;font-weight:400;letter-spacing:3px}
.btn{position:absolute;display:flex;align-items:center;justify-content:center;border-radius:30px;background:var(--grad);color:#fff;font-weight:700;font-size:15px;text-transform:uppercase}
.brand{display:flex;align-items:center;gap:12px;font-family:"Michroma",sans-serif;color:var(--navy);font-size:30px;letter-spacing:4px}
.brand-dot{width:38px;height:38px;border-radius:50%;background:var(--navy)}

/* header */
.header{position:absolute;left:0;top:0;width:1200px;height:113px;background:#fff}
.nav{position:absolute;top:48px;display:flex;font-size:14px;font-weight:700;color:var(--ink)}
.nav span{position:absolute;white-space:nowrap}
.nav .active{color:var(--teal);text-decoration:underline}

/* hero */
.hero-title{position:absolute;left:0;width:1200px;top:292px;text-align:center;color:#fff;font-size:27px;line-height:42px}
.hero-sub{position:absolute;left:300px;width:600px;top:380px;text-align:center;color:#fff;font-size:18px;line-height:29px;font-weight:500}
.follow{position:absolute;left:1138px;top:210px;width:36px;height:96px;color:#fff;font-size:12px;font-weight:700;writing-mode:vertical-rl;display:flex;align-items:center;justify-content:center;letter-spacing:.5px}
.soc{position:absolute;left:1137px;width:36px;height:36px;border-radius:50%;border:1.5px solid #fff;background:rgba(255,255,255,.15)}
.soc.on{background:var(--teal);border-color:var(--teal)}

/* headings */
.sec-title{position:absolute;left:0;width:1200px;text-align:center;color:var(--navy);font-size:27px}
.sec-title::after{content:"";display:block;width:72px;height:3px;background:var(--teal);margin:16px auto 0}
.copy{font-size:15.5px;line-height:27.5px;text-align:justify}
.copy p+p{margin-top:14px}

/* products */
.tab{position:absolute;top:1694px;width:358px;height:94px;border-radius:47px;display:flex;align-items:center;font-weight:700;font-size:20px}
.tab .icon{width:74px;height:74px;border-radius:50%;margin:0 10px;display:flex;align-items:center;justify-content:center}
.tab.active{left:232px;background:var(--grad);color:#fff}
.tab.active .icon{background:#fff}
.tab.idle{left:608px;background:#fff;color:var(--navy);box-shadow:0 6px 18px rgba(30,40,100,.12)}
.tab.idle .icon{background:var(--grad)}

/* blog */
.card{position:absolute;top:2530px;width:308px;height:425px;background:#fff;box-shadow:0 4px 16px rgba(20,30,80,.12);border-radius:4px}
.card .photo{position:absolute;left:6px;top:6px;width:296px;height:196px}
.card .date{position:absolute;left:20px;top:230px;font-size:13px;color:var(--ink);display:flex;align-items:center;gap:8px}
.card h3{position:absolute;left:20px;width:270px;top:254px;font-size:16px;line-height:25px;color:var(--navy);font-weight:700;text-transform:uppercase}
.card p{position:absolute;left:20px;width:270px;top:312px;font-size:13px;line-height:23px;text-align:justify}
.card .more{position:absolute;left:20px;top:384px;font-size:12.5px;font-weight:700;color:var(--teal-soft);display:flex;align-items:center;gap:8px}

/* contact */
.form-label{position:absolute;font-size:15px;font-weight:700;color:var(--ink)}
.form-field{position:absolute;font-size:12.5px;color:#8a8e98;border-bottom:1px solid var(--line);padding-bottom:14px}

/* footer */
.foot-head{position:absolute;top:3793px;font-size:18px;font-weight:700;color:var(--navy)}
.foot-head::after{content:"";display:block;width:112px;height:3px;background:var(--teal);margin-top:12px}
.foot-list{position:absolute;top:3855px;font-size:14.5px;color:var(--ink);line-height:39px;list-style:none}
.foot-follow{position:absolute;left:950px;display:flex;align-items:center;gap:18px;font-size:14.5px;color:var(--ink);line-height:24px}
.foot-follow .dot{width:36px;height:36px;border-radius:50%;background:var(--grad)}
</style>
</head>
<body>
<div class="canvas">

  <!-- header -->
  <header class="header">
    <div class="brand abs" style="left:112px;top:36px"><span class="brand-dot"></span>VORTEQ</div>
    <nav class="nav">
      <span class="active" style="left:467px">HOME</span>
      <span style="left:538px">OUR PRODUCTS</span>
      <span style="left:676px">ABOUT US</span>
      <span style="left:775px">BLOG</span>
      <span style="left:841px">CONTACT</span>
    </nav>
    <div class="btn" style="left:940px;top:32px;width:148px;height:48px">Get a Quote</div>
  </header>

  <!-- hero -->
  <section>
    <svg class="abs" style="left:0;top:113px" width="1200" height="650" viewBox="0 113 1200 650">
      <defs>
        <linearGradient id="heroFill" x1="0" y1="0" x2="1" y2="1">
          <stop offset="0" stop-color="#8c7a5c"/>
          <stop offset=".45" stop-color="#5d7f93"/>
          <stop offset="1" stop-color="#c9d4da"/>
        </linearGradient>
      </defs>
      <rect x="0" y="113" width="1200" height="650" fill="url(#heroFill)" role="img" aria-label="Photo of a team working together on laptops"/>
      <rect x="0" y="113" width="1200" height="650" fill="#1b2a4a" opacity=".28"/>
      <polygon points="60,548 520,700 0,725" fill="#eef6f8" opacity=".75"/>
      <polygon points="0,618 500,700 905,753 1200,602 1200,763 0,763" fill="#fff"/>
      <polygon points="970,705 1200,590 1200,646 1046,724" fill="var(--navy)"/>
    </svg>
    <h1 class="hero-title display">INNOVATIVE PRODUCTS FOR<br>EVERYDAY LIFE.</h1>
    <p class="hero-sub">Lorem ipsum dolor sit amet, consectetur adipiscing elit, sed do eiusmod tempor incididunt ut laborea.</p>
    <div class="btn" style="left:523px;top:460px;width:154px;height:46px;font-size:14px">Get Started</div>
    <div class="follow">FOLLOW US ON</div>
    <span class="soc" style="top:330px"></span>
    <span class="soc on" style="top:374px"></span>
    <span class="soc" style="top:420px"></span>
  </section>

  <!-- about -->
  <section>
    <h2 class="sec-title display" style="top:808px">ABOUT VORTEQ</h2>
    <p class="abs" style="left:108px;width:984px;top:874px;text-align:center;font-size:16px;line-height:28px;color:var(--ink);font-weight:500">Lorem ipsum dolor sit amet, consectetur adipiscing elit, sed do eiusmod tempor incididunt ut labore et dolore magna aliqua. Ut enim ad minim veniam, quis nostrud exercitation ullamco laboris nisi ut aliquip ex ea commodo consequat. Duis aute irure dolor in reprehenderit in voluptate velit esse cillum dolore eu fugiat nulla pariatureа.</p>
    <div class="copy abs" style="left:112px;width:488px;top:1019px">
      <p>Lorem ipsum dolor sit amet, consectetur adipiscing elit, sed do eiusmod tempor incididunt ut labore et dolore magna aliqua. Ut enim ad minim veniam, quis nostrud exercitation ullamco laboris nisi ut aliquip ex ea commodo consequat. Duis aute irure dolor in reprehend in voluptate velit esse cillum dolorea.</p>
      <p>Lorem ipsum dolor sit amet, consectetur adipiscing elit, sed do eiusmod tempor incididunt ut labore et dolore magna aliqua. Ut enim ad minim veniam, quis nostrud exercitation ullamco laboris nisi ut aliquip ex ea commodo consequat duis aute irurea.</p>
    </div>
    <div class="btn" style="left:112px;top:1305px;width:146px;height:46px;font-size:14px">Learn More</div>
    <svg class="abs" style="left:640px;top:960px" width="460" height="460">
      <defs>
        <linearGradient id="teamFill" x1="0" y1="0" x2="1" y2="1">
          <stop offset="0" stop-color="#9fb5a8"/><stop offset=".5" stop-color="#c9c2b8"/><stop offset="1" stop-color="#6d6a70"/>
        </linearGradient>
      </defs>
      <path d="M68 46 L420 22 Q448 20 448 48 L448 420 Q448 448 420 448 L90 448 Q62 448 62 420 Z" fill="#ebecf2"/>
      <path d="M32 48 Q12 50 12 72 L12 386 Q12 412 38 412 L386 412 Q412 412 412 386 L412 34 Q412 8 386 10 Z" fill="url(#teamFill)" role="img" aria-label="Photo of a smiling team gathered around a desk"/>
    </svg>
  </section>

  <!-- products -->
  <section>
    <svg class="abs" style="left:0;top:1420px" width="1200" height="965">
      <polygon points="0,210 300,5 1200,125 1200,965 0,965" fill="var(--mist)"/>
      <polygon points="0,210 160,33 232,56 0,195" fill="var(--teal)"/>
    </svg>
    <h2 class="sec-title display" style="top:1617px">OUR PRODUCTS</h2>
    <div class="tab active">
      <span class="icon"><svg width="38" height="38" viewBox="0 0 38 38"><path d="M5 14 L9 5 H29 L33 14 Z" fill="var(--navy)"/><rect x="7" y="15" width="24" height="18" fill="var(--navy)"/><rect x="11" y="20" width="7" height="13" fill="#fff"/><rect x="21" y="20" width="6" height="5" fill="#fff"/></svg></span>
      <span style="margin-left:14px">LAUNDRY MARKETS</span>
    </div>
    <svg class="abs" style="left:400px;top:1786px" width="24" height="14"><polygon points="0,0 24,0 12,14" fill="#1f3f8e"/></svg>
    <div class="tab idle">
      <span class="icon"><svg width="36" height="36" viewBox="0 0 36 36"><rect x="8" y="5" width="20" height="26" rx="3" fill="#fff"/><circle cx="18" cy="20" r="4" fill="var(--navy)"/><circle cx="13" cy="14" r="2" fill="var(--navy)"/><circle cx="18" cy="12" r="2" fill="var(--navy)"/><circle cx="23" cy="14" r="2" fill="var(--navy)"/></svg></span>
      <span style="margin-left:14px">PET TREAT PRODUCTS</span>
    </div>
    <svg class="abs" style="left:110px;top:1853px" width="448" height="448">
      <defs>
        <linearGradient id="ring" x1="0" y1="0" x2="0" y2="1"><stop offset="0" stop-color="var(--teal)"/><stop offset="1" stop-color="var(--navy)"/></linearGradient>
        <linearGradient id="laundryFill" x1="0" y1="0" x2="1" y2="1"><stop offset="0" stop-color="#a9c79a"/><stop offset=".55" stop-color="#e4e6e4"/><stop offset="1" stop-color="#9c7c5c"/></linearGradient>
      </defs>
      <circle cx="224" cy="224" r="223" fill="url(#ring)"/>
      <circle cx="224" cy="236" r="210" fill="url(#laundryFill)" role="img" aria-label="Photo of a washing machine, detergent bottle and folded towels"/>
    </svg>
    <h2 class="abs" style="left:598px;top:1872px;font-size:34px;color:var(--navy);font-weight:700">LAUNDRY MARKETS</h2>
    <div class="copy abs" style="left:600px;width:488px;top:1935px">
      <p>Lorem ipsum dolor sit amet, consectetur adipiscing elit, sed do eiusmod tempor incididunt ut labore et dolore magna aliqua. Ut enim ad minim veniam, quis nostrud exercitation ullamco laboris nisi ut aliquip ex ea commodo consequat. Duis aute irure dolor in reprehend in voluptate velit esse cillum dolorea.</p>
      <p>Lorem ipsum dolor sit amet, consectetur adipiscing elit, sed do eiusmod tempor incididunt ut labore et dolore magna aliqua. Ut enim ad minim veniam, quis nostrud exercitation ullamco laboris nisi ut aliquip ex ea commodo consequat duis aute irurea.</p>
    </div>
    <div class="btn" style="left:600px;top:2224px;width:180px;height:48px;font-size:14px">Pre-Order Now</div>
  </section>

  <!-- blog -->
  <section>
    <div class="abs" style="left:0;top:2383px;width:1200px;height:348px;background:linear-gradient(100deg,var(--navy-deep) 0%,#1d4d93 55%,var(--teal) 100%)"></div>
    <h2 class="sec-title display" style="top:2444px;color:#fff">LATEST BLOG</h2>

    <article class="card" style="left:112px">
      <div class="photo" style="background:linear-gradient(135deg,#c8ccd2,#8a94a0)" role="img" aria-label="Photo of a team meeting in a bright office"></div>
      <div class="date"><svg width="12" height="12"><rect x="1" y="2" width="10" height="9" rx="1" fill="none" stroke="var(--teal)" stroke-width="1.5"/></svg>04 Apr 2025</div>
      <h3>Lorem ipsum dolor sit amet consecte adipea</h3>
      <p>Lorem ipsum dolor sit amet, consectetur adipiscing elit, sed do eiusmod tempor incidi dunt ut labore et dolore magna.</p>
      <div class="more">READ MORE <svg width="12" height="12"><circle cx="6" cy="6" r="6" fill="var(--teal-soft)"/><path d="M5 3.5 L7.5 6 L5 8.5" stroke="#fff" stroke-width="1.5" fill="none"/></svg></div>
    </article>
    <article class="card" style="left:446px">
      <div class="photo" style="background:linear-gradient(135deg,#d7d9dc,#7d858c)" role="img" aria-label="Photo of a presenter at a whiteboard with colleagues"></div>
      <div class="date"><svg width="12" height="12"><rect x="1" y="2" width="10" height="9" rx="1" fill="none" stroke="var(--teal)" stroke-width="1.5"/></svg>04 Apr 2025</div>
      <h3>Lorem ipsum dolor sit amet consecte adipea</h3>
      <p>Lorem ipsum dolor sit amet, consectetur adipiscing elit, sed do eiusmod tempor incidi dunt ut labore et dolore magna.</p>
      <div class="more">READ MORE <svg width="12" height="12"><circle cx="6" cy="6" r="6" fill="var(--teal-soft)"/><path d="M5 3.5 L7.5 6 L5 8.5" stroke="#fff" stroke-width="1.5" fill="none"/></svg></div>
    </article>
    <article class="card" style="left:780px">
      <div class="photo" style="background:linear-gradient(135deg,#e4e5e3,#a89c8a)" role="img" aria-label="Photo of a woman working at a desk by a window"></div>
      <div class="date"><svg width="12" height="12"><rect x="1" y="2" width="10" height="9" rx="1" fill="none" stroke="var(--teal)" stroke-width="1.5"/></svg>04 Apr 2025</div>
      <h3>Lorem ipsum dolor sit amet consecte adipea</h3>
      <p>Lorem ipsum dolor sit amet, consectetur adipiscing elit, sed do eiusmod tempor incidi dunt ut labore et dolore magna.</p>
      <div class="more">READ MORE <svg width="12" height="12"><circle cx="6" cy="6" r="6" fill="var(--teal-soft)"/><path d="M5 3.5 L7.5 6 L5 8.5" stroke="#fff" stroke-width="1.5" fill="none"/></svg></div>
    </article>
    <div class="btn" style="left:488px;top:3001px;width:222px;height:48px;font-size:14px">View More Blog Post</div>
  </section>

  <!-- contact -->
  <section>
    <div class="abs" style="left:108px;top:3141px;width:448px;height:384px;background:linear-gradient(135deg,#262f86,#1e2670)"></div>
    <div class="abs" style="left:742px;top:3160px;width:366px;height:348px;border:4px solid var(--teal)"></div>
    <p class="abs display" style="left:140px;width:278px;top:3243px;text-align:right;color:#fff;font-size:13px">CONTACT US</p>
    <p class="abs" style="left:140px;width:278px;top:3290px;text-align:right;color:#fff;font-size:36px;font-weight:700;line-height:53px">LET’S DO<br>GOOD<br>TOGETHER!</p>
    <div class="abs" style="left:462px;top:3192px;width:625px;height:433px;background:#fff;box-shadow:0 6px 26px rgba(20,30,80,.12)"></div>
    <p class="abs display" style="left:515px;top:3240px;color:var(--navy);font-size:14px">SEND US A MESSAGE</p>
    <span class="form-label" style="left:518px;top:3298px">First Name</span>
    <span class="form-field" style="left:518px;top:3331px;width:230px">Ethan</span>
    <span class="form-label" style="left:795px;top:3298px">Last Name</span>
    <span class="form-field" style="left:795px;top:3331px;width:230px">Marlow</span>
    <span class="form-label" style="left:518px;top:3391px">Email Address</span>
    <span class="form-field" style="left:518px;top:3424px;width:230px">ethanmarlow@inboxly.com</span>
    <span class="form-label" style="left:795px;top:3391px">Phone</span>
    <span class="form-field" style="left:795px;top:3424px;width:230px">+1 (555) 014 2233</span>
    <span class="form-label" style="left:518px;top:3484px">Message</span>
    <span class="form-field" style="left:518px;top:3517px;width:450px;padding-bottom:32px">Lorem ipsum dolor sit a tetur adipiscing...|</span>
    <svg class="abs" style="left:963px;top:3517px" width="64" height="64">
      <defs><linearGradient id="sendG" x1="0" y1="1" x2="1" y2="0"><stop offset="0" stop-color="var(--navy)"/><stop offset="1" stop-color="var(--teal)"/></linearGradient></defs>
      <circle cx="32" cy="32" r="32" fill="url(#sendG)"/>
      <path d="M22 34 L43 22 L36 43 L32 35 Z" fill="#fff"/>
    </svg>
  </section>

  <!-- footer -->
  <footer>
    <div class="abs" style="left:0;top:3733px;width:1200px;height:372px;background:var(--foot)"></div>
    <div class="brand abs" style="left:112px;top:3886px"><span class="brand-dot"></span>VORTEQ</div>
    <h4 class="foot-head" style="left:500px">NAVIGATION</h4>
    <ul class="foot-list" style="left:502px"><li>Home</li><li>Our Products</li><li>About Us</li><li>Blog</li><li>Contact</li></ul>
    <h4 class="foot-head" style="left:715px">QUICK LINKS</h4>
    <ul class="foot-list" style="left:716px"><li>Privacy Policy</li><li>Terms Of Services</li><li>FAQ</li><li>Disclaimer</li></ul>
    <h4 class="foot-head" style="left:950px">FOLLOW US</h4>
    <div class="foot-follow" style="top:3858px"><span class="dot"></span><span>Follow Us On<br>FRIENDSPACE</span></div>
    <div class="foot-follow" style="top:3918px"><span class="dot"></span><span>Follow Us On<br>CHIRPLINE</span></div>
    <div class="foot-follow" style="top:3978px"><span class="dot"></span><span>Follow Us On<br>WORKNET</span></div>
    <div class="abs" style="left:112px;top:4055px;width:976px;height:1px;background:var(--line)"></div>
    <p class="abs" style="left:0;width:1200px;top:4072px;text-align:center;font-size:13px;color:var(--ink)">Copyright © 2025 Vorteq - All Rights Reserved.</p>
  </footer>

</div>
</body>
</html>
```